Web portal for events

The project is about creating a web application - portal for culture events in Denmark.

Design

We aim for very simplistic, light and fully responsive design. The white background is preferable, as well as light color tones. As inspirational points we like the colors used in www.parvolio.com and www.brindlemoor.org

FORMAT AND REQUIREMENTS:
1. Design should be provided based on the wireframes specified as a link below.
2. The design (and all of its pages) should be provided in three resolution variants:
- Desktop
- Tablet
- Phone
3. The design should be provided as PSD, where each page/section should be in its own PSD file
4. All graphical elements in the design should be delivered as single layers which can then be extracted from the PSD.
5. All graphical elements (icons, graphical buttons, etc.) should be provided as vector objects in the PSD, so that they can be exported into different sizes without loss of quality (for responsiveness)
6. The design should use either web safe fonts or Google Fonts.

RESPONSIVENESS
The web application should be visible on any devices (i.e. responsive design)

WIREFRAMES:
https://velkotrams.examplewire.com/projects/fennoplex/prototype/Homepage?key=3b7c19d0f2a84e6c5d1e9a07b4f2c8d6e1a3f590

We expect design of the following wireframes:

Homepage:
https://velkotrams.examplewire.com/projects/fennoplex/Homepage

For arrangører - billede uploaded:
https://velkotrams.examplewire.com/projects/fennoplex/For%20arrang%C3%B8rer%20-%20billede%20uploaded

Further specifications of the project (i.e. functionality, etc.):
https://files.quorvane.net/document/d/8pKw_Rt2mZqLx4NvB7yHc0aEs9uGdJf3TiOb6nVlW1k/edit?usp=sharing

```html
<!DOCTYPE html>
<html lang="da">
<head>
<meta charset="utf-8">
<title>KULTRA – din guide til kultur og events</title>
<link href="https://fonts.googleapis.com/css2?family=Roboto+Condensed:wght@400;700&family=Arimo:wght@400;700&family=Poppins:wght@500&display=swap" rel="stylesheet">
<style>
:root{
  --brand:#ff3d12;
  --brand-dark:#d9350f;
  --ink:#333333;
  --muted:#9a9a9a;
  --line:#dddddd;
  --panel:#e4e4e4;
  --white:#ffffff;
}
*{box-sizing:border-box;margin:0;padding:0}
html,body{width:1200px;height:2174px;overflow:hidden;background:var(--white)}
body{position:relative;font-family:"Arimo",Arial,sans-serif;color:var(--ink)}
h2,h3{font-weight:400}
.abs{position:absolute}

/* header */
.site-header{position:absolute;left:0;top:0;width:1200px;height:115px;background:var(--brand)}
.brand-name{position:absolute;left:130px;top:12px;font-family:"Poppins",sans-serif;font-weight:500;font-size:58px;letter-spacing:2px;color:var(--white);line-height:1}
.brand-tag{position:absolute;left:132px;top:78px;font-size:16px;color:var(--white)}
.search{position:absolute;left:378px;top:36px;width:447px;height:42px;border:1.5px solid var(--white);border-radius:21px;color:var(--white);font-size:14px;font-weight:700;padding:12px 0 0 36px}
.search svg{position:absolute;left:13px;top:13px}
.btn-outline{position:absolute;top:36px;height:42px;border:1.5px solid var(--white);border-radius:21px;color:var(--white);font-size:13px;font-weight:700;text-align:center;line-height:39px}
.main-nav{position:absolute;left:0;top:115px;width:1200px;height:63px;background:var(--brand-dark)}
.main-nav a{position:absolute;top:23px;transform:translateX(-50%);font-family:"Roboto Condensed",sans-serif;font-size:15px;color:var(--white);text-decoration:none}

/* hero */
.hero{position:absolute;left:130px;top:180px;width:939px;height:455px;background:radial-gradient(ellipse at 45% 20%,#8b9aa6 0%,#3a3d44 35%,#151517 70%),#111;overflow:hidden}
.hero::before{content:"";position:absolute;inset:0;background:radial-gradient(circle at 8% 20%,rgba(200,20,30,.55),transparent 30%),radial-gradient(circle at 95% 15%,rgba(210,20,30,.5),transparent 25%)}
.hero-caption{position:absolute;left:27px;top:406px;font-size:11.5px;line-height:22px;color:var(--white)}
.hero-arrow{position:absolute;top:592px;width:30px;height:30px;border-radius:50%;background:rgba(255,255,255,.55)}

/* section headings */
.section-title{position:absolute;font-family:"Roboto Condensed",sans-serif;font-weight:400;font-size:23px;color:#3a3a3a}
.intro{position:absolute;left:130px;top:710px;width:636px;text-align:center;font-size:11px;line-height:21px;color:var(--muted)}

/* filters */
.filter{position:absolute;top:778px;height:34px;border:1px solid #cfcfcf;font-family:"Roboto Condensed",sans-serif;font-size:13px;color:#666;text-align:center;line-height:32px}
.filter.is-active{background:var(--panel);border-color:var(--panel)}

/* event cards */
.event-card{position:absolute;width:206px}
.event-photo{width:206px;height:135px;border:1px solid var(--line);padding:5px}
.event-photo div{width:100%;height:100%}
.event-title{margin-top:18px;font-size:12.5px;font-weight:400;color:#444}
.event-text{margin-top:9px;font-size:11px;line-height:18px;color:var(--muted)}
.event-meta{margin-top:8px;border-top:1px dashed #bbb;border-bottom:1px dashed #bbb;padding:9px 0 10px;font-size:10.5px;color:#333}
.event-meta span{color:var(--brand)}

/* pagination */
.pager{position:absolute;top:2003px;font-size:16px;font-weight:700;color:#222;transform:translateX(-50%)}
.pager.is-current{color:var(--brand)}

/* sidebar */
.fav-item{position:absolute;left:790px;width:280px}
.fav-thumb{position:absolute;left:0;top:0;width:84px;height:80px;border:1px solid var(--line);padding:4px}
.fav-thumb div{width:100%;height:100%}
.fav-title{position:absolute;left:97px;top:4px;font-size:12.5px;color:#333}
.fav-text{position:absolute;left:97px;top:27px;width:170px;font-size:11px;line-height:19px;color:var(--muted)}
.btn-solid{position:absolute;background:var(--brand);color:var(--white);border-radius:18px;text-align:center}

.newsletter{position:absolute;left:788px;top:1240px;width:280px;height:292px;border:1px solid var(--line)}
.newsletter-inner{position:absolute;left:11px;top:9px;width:259px;height:274px;border:1px solid var(--line)}
.newsletter-text{position:absolute;left:22px;top:24px;width:236px;font-size:11px;line-height:19px;color:var(--muted)}
.field{position:absolute;left:21px;width:236px;height:42px;border:1px solid #cfcfcf;font-size:11px;color:#666;padding:14px 0 0 12px}

/* footer */
.site-footer{position:absolute;left:0;top:2058px;width:1200px;height:116px;background:var(--brand)}
.footer-links{position:absolute;left:130px;top:34px;font-size:12px;color:var(--white);word-spacing:2px}
.footer-links span{margin:0 8px}
.copyright{position:absolute;left:130px;top:73px;font-size:12px;color:var(--white)}
.social{position:absolute;top:45px;width:30px;height:30px;border:1.5px solid var(--white);border-radius:50%}
</style>
</head>
<body>

<header class="site-header">
  <div class="brand-name">KULTRA</div>
  <div class="brand-tag">din guide til kultur og events</div>
  <div class="search">
    <svg width="13" height="13" viewBox="0 0 13 13"><circle cx="5" cy="5" r="4" fill="none" stroke="#fff" stroke-width="2"/><line x1="8" y1="8" x2="12" y2="12" stroke="#fff" stroke-width="2"/></svg>
    SEARCH
  </div>
  <div class="btn-outline" style="left:842px;width:107px">LOGIN</div>
  <div class="btn-outline" style="left:961px;width:108px">REGISTER</div>
</header>

<nav class="main-nav">
  <a style="left:161px">ALLE</a>
  <a style="left:258px">MUSIK</a>
  <a style="left:359px">SPORT</a>
  <a style="left:465px">TEATER</a>
  <a style="left:586px">UDSTILLING</a>
  <a style="left:708px">AELDRE</a>
  <a style="left:810px">BORN</a>
  <a style="left:914px">MOTION</a>
  <a style="left:1026px">DIVERSE</a>
</nav>

<section class="hero" role="img" aria-label="Koncertscene med spotlys og publikum">
  <p class="hero-caption">Sed ut perspiciatis unde omnis iste natus error sit voluptatem accusantium doloremque laudantium totam rem aperiam,<br>eaque ipsa quae ab illo inventore veritatis et quasi architecto beatae vitae dicta sunt explicabo.</p>
</section>
<svg class="hero-arrow" style="left:989px" viewBox="0 0 30 30"><polyline points="18,8 11,15 18,22" fill="none" stroke="#333" stroke-width="3"/></svg>
<svg class="hero-arrow" style="left:1025px" viewBox="0 0 30 30"><polyline points="12,8 19,15 12,22" fill="none" stroke="#333" stroke-width="3"/></svg>

<h2 class="section-title" style="left:358px;top:668px">POPULARE EVENTS</h2>
<p class="intro">Sed ut perspiciatis unde omnis iste natus error sit voluptatem accusantium doloremque laudantium, totam rem aperiam,<br>eaque ipsa quae ab illo inventore veritatis et quasi architecto beatae vitae dicta sunt explicabo</p>

<div class="filter is-active" style="left:194px;width:109px">POPULAERE</div>
<svg class="abs" style="left:237px;top:811px" width="14" height="8"><polygon points="0,0 14,0 7,7" fill="#e4e4e4"/></svg>
<div class="filter" style="left:325px;width:109px;text-align:left;padding-left:10px">OMRADE</div>
<svg class="abs" style="left:400px;top:778px" width="34" height="34"><line x1="0.5" y1="0" x2="0.5" y2="34" stroke="#cfcfcf"/><polygon points="12,14 22,14 17,20" fill="#666"/></svg>
<div class="filter" style="left:454px;width:108px">DATO</div>
<div class="filter" style="left:584px;width:109px">PRIS</div>

<!-- row 1 -->
<article class="event-card" style="left:130px;top:865px"><div class="event-photo"><div role="img" aria-label="Havnefront med statue ved vandet" style="background:linear-gradient(#8fb7dc,#5a7e98 55%,#6d7a82)"></div></div><h3 class="event-title">ASGER NYLUND KONCERT</h3><p class="event-text">Lorem ipsum dolor sit amet, consectetuer adipiscing elit.</p><p class="event-meta">Se Events 20May 2014 , <span>Mine Favoritter</span></p></article>
<article class="event-card" style="left:349px;top:865px"><div class="event-photo"><div role="img" aria-label="Slot ved havnen" style="background:linear-gradient(#a9c6e0,#8a8f7d 55%,#7a8a6a)"></div></div><h3 class="event-title">ASGER NYLUND KONCERT</h3><p class="event-text">Lorem ipsum dolor sit amet, consectetuer adipiscing elit.</p><p class="event-meta">Se Events 20May 2014 , <span>Mine Favoritter</span></p></article>
<article class="event-card" style="left:568px;top:865px"><div class="event-photo"><div role="img" aria-label="Oplyst bytorv om aftenen" style="background:linear-gradient(#1f2f5c,#6a5a48 60%,#b59870)"></div></div><h3 class="event-title">ASGER NYLUND KONCERT</h3><p class="event-text">Lorem ipsum dolor sit amet, consectetuer adipiscing elit.</p><p class="event-meta">Se Events 20May 2014 , <span>Mine Favoritter</span></p></article>
<!-- row 2 -->
<article class="event-card" style="left:130px;top:1148px"><div class="event-photo"><div role="img" aria-label="Venner der hopper på stranden" style="background:linear-gradient(#a8d4ec,#cfe3ec 60%,#d9ccb0)"></div></div><h3 class="event-title">ASGER NYLUND KONCERT</h3><p class="event-text">Lorem ipsum dolor sit amet, consectetuer adipiscing elit.</p><p class="event-meta">Se Events 20May 2014 , <span>Mine Favoritter</span></p></article>
<article class="event-card" style="left:349px;top:1148px"><div class="event-photo"><div role="img" aria-label="Kanal med træer og bygninger" style="background:linear-gradient(#6ea0d8,#6b7a5a 50%,#3e5a72)"></div></div><h3 class="event-title">ASGER NYLUND KONCERT</h3><p class="event-text">Lorem ipsum dolor sit amet, consectetuer adipiscing elit.</p><p class="event-meta">Se Events 20May 2014 , <span>Mine Favoritter</span></p></article>
<article class="event-card" style="left:568px;top:1148px"><div class="event-photo"><div role="img" aria-label="Glad vennegruppe udendørs" style="background:linear-gradient(#7fb0e0,#b8a090 60%,#6a80a8)"></div></div><h3 class="event-title">ASGER NYLUND KONCERT</h3><p class="event-text">Lorem ipsum dolor sit amet, consectetuer adipiscing elit.</p><p class="event-meta">Se Events 20May 2014 , <span>Mine Favoritter</span></p></article>
<!-- row 3 -->
<article class="event-card" style="left:130px;top:1433px"><div class="event-photo"><div role="img" aria-label="Klippekyst i solnedgang" style="background:linear-gradient(#d8a070,#9a8070 50%,#b0a8a0)"></div></div><h3 class="event-title">ASGER NYLUND KONCERT</h3><p class="event-text">Lorem ipsum dolor sit amet, consectetuer adipiscing elit.</p><p class="event-meta">Se Events 20May 2014 , <span>Mine Favoritter</span></p></article>
<article class="event-card" style="left:349px;top:1433px"><div class="event-photo"><div role="img" aria-label="Kvinde foran springvand" style="background:linear-gradient(#c8d0d0,#b8a890 60%,#8a8070)"></div></div><h3 class="event-title">ASGER NYLUND KONCERT</h3><p class="event-text">Lorem ipsum dolor sit amet, consectetuer adipiscing elit.</p><p class="event-meta">Se Events 20May 2014 , <span>Mine Favoritter</span></p></article>
<article class="event-card" style="left:568px;top:1433px"><div class="event-photo"><div role="img" aria-label="Cykeltur i grønt landskab" style="background:linear-gradient(#a8c8e8,#c0d0d8 45%,#6a9a3a)"></div></div><h3 class="event-title">ASGER NYLUND KONCERT</h3><p class="event-text">Lorem ipsum dolor sit amet, consectetuer adipiscing elit.</p><p class="event-meta">Se Events 20May 2014 , <span>Mine Favoritter</span></p></article>
<!-- row 4 -->
<article class="event-card" style="left:130px;top:1716px"><div class="event-photo"><div role="img" aria-label="Slot spejlet i sø" style="background:linear-gradient(#8ab0d8,#5a6a40 50%,#4a5a48)"></div></div><h3 class="event-title">ASGER NYLUND KONCERT</h3><p class="event-text">Lorem ipsum dolor sit amet, consectetuer adipiscing elit.</p><p class="event-meta">Se Events 20May 2014 , <span>Mine Favoritter</span></p></article>
<article class="event-card" style="left:349px;top:1716px"><div class="event-photo"><div role="img" aria-label="Slotsgård med springvand" style="background:linear-gradient(#e8e8e8,#8a6a58 50%,#6a6058)"></div></div><h3 class="event-title">ASGER NYLUND KONCERT</h3><p class="event-text">Lorem ipsum dolor sit amet, consectetuer adipiscing elit.</p><p class="event-meta">Se Events 20May 2014 , <span>Mine Favoritter</span></p></article>
<article class="event-card" style="left:568px;top:1716px"><div class="event-photo"><div role="img" aria-label="Palæfacade på plads" style="background:linear-gradient(#6a9ad8,#c8b898 45%,#a89878)"></div></div><h3 class="event-title">ASGER NYLUND KONCERT</h3><p class="event-text">Lorem ipsum dolor sit amet, consectetuer adipiscing elit.</p><p class="event-meta">Se Events 20May 2014 , <span>Mine Favoritter</span></p></article>

<!-- pagination -->
<span class="pager" style="left:252px;font-weight:400;font-size:13px;top:2005px">«</span>
<span class="pager" style="left:273px">1</span>
<span class="pager" style="left:308px">2</span>
<span class="pager" style="left:343px">3</span>
<span class="pager" style="left:378px">4</span>
<span class="pager" style="left:413px">5</span>
<span class="pager" style="left:448px">6</span>
<span class="pager is-current" style="left:483px">7</span>
<span class="pager" style="left:518px">8</span>
<span class="pager" style="left:553px">9</span>
<span class="pager" style="left:577px;font-weight:400;font-size:13px;top:2005px">»</span>
<svg class="abs" style="left:260px;top:2022px" width="320" height="14"><path d="M10 12 Q160 4 310 12" fill="none" stroke="#d6d6d6"/><polygon points="218,4 223,11 213,11" fill="#222"/></svg>

<!-- sidebar -->
<h2 class="section-title" style="left:788px;top:668px">MINE&nbsp; FAVORITTER</h2>
<div class="fav-item" style="top:714px;height:80px"><div class="fav-thumb"><div role="img" aria-label="Skib i havn" style="background:linear-gradient(#8aa0b8,#506070)"></div></div><p class="fav-title">NEQUE PORRO QUISQUAM</p><p class="fav-text">Perspiciatis unde omnis iste natus error sit voluptatem accusantium doloremque....</p></div>
<div class="fav-item" style="top:816px;height:80px"><div class="fav-thumb"><div role="img" aria-label="Slot ved kysten" style="background:linear-gradient(#a8c8e8,#a89070 60%,#6a88a0)"></div></div><p class="fav-title">NEQUE PORRO QUISQUAM</p><p class="fav-text">Perspiciatis unde omnis iste natus error sit voluptatem accusantium doloremque....</p></div>
<div class="fav-item" style="top:918px;height:80px"><div class="fav-thumb"><div role="img" aria-label="Hvide kridtklinter ved havet" style="background:linear-gradient(90deg,#3a70b0,#e8eef2 60%,#6a9040)"></div></div><p class="fav-title">NEQUE PORRO QUISQUAM</p><p class="fav-text">Perspiciatis unde omnis iste natus error sit voluptatem accusantium doloremque....</p></div>
<div class="fav-item" style="top:1020px;height:80px"><div class="fav-thumb"><div role="img" aria-label="Herregård med have" style="background:linear-gradient(#6a9ad8,#a87860 55%,#5a8a38)"></div></div><p class="fav-title">NEQUE PORRO QUISQUAM</p><p class="fav-text">Perspiciatis unde omnis iste natus error sit voluptatem accusantium doloremque....</p></div>
<div class="btn-solid" style="left:907px;top:1129px;width:162px;height:35px;line-height:35px;font-size:11.5px">SE MINE &nbsp;FAVORITTER</div>
<svg class="abs" style="left:788px;top:1186px" width="282" height="2"><line x1="0" y1="1" x2="282" y2="1" stroke="#dddddd"/></svg>

<h2 class="section-title" style="left:788px;top:1204px">MYHEDSBREV</h2>
<div class="newsletter">
  <div class="newsletter-inner"></div>
  <p class="newsletter-text">Sed ut perspiciatis unde omnis iste natus error sitvoluptatem accusantium doloremque , totam aperiam, eaque ipsa tecto beatae vitae dicta sunt explicabo....</p>
  <div class="field" style="top:113px">Enter Your Name :</div>
  <div class="field" style="top:165px">Enter Your Email :</div>
  <div class="btn-solid" style="left:67px;top:231px;width:145px;height:36px;line-height:36px;font-size:15px">SUBSCRIBE</div>
</div>

<footer class="site-footer">
  <p class="footer-links">Alle<span>|</span>Musik<span>|</span>Sport<span>|</span>Teater<span>|</span>Udstilling<span>|</span>Aeldre<span>|</span>Born<span>|</span>Motion<span>|</span>Diverse</p>
  <p class="copyright">© Copy Rights 2014 Denmark.All Rights Reserved.</p>
  <span class="social" style="left:886px"></span>
  <span class="social" style="left:922px"></span>
  <span class="social" style="left:959px"></span>
  <span class="social" style="left:995px"></span>
  <span class="social" style="left:1031px"></span>
</footer>

</body>
</html>
```